Otter Bites Guild - A Monthly Subscription Dog Treats Club - Shopify Website Design

A monthly subscription company. Need a Shopify Website Design and uploaded to fully work with Crisp Renewals.

Please look at these sites for examples as well as the images I enclosed.

https://www.mealbrightly.com/
https://www.globalmunchbox.com/

Number of Pages Required

1 page

```html
<!DOCTYPE html>
<html lang="en">
<head>
<meta charset="utf-8">
<title>Otter Bites Guild – Monthly Subscription of Dog Treats</title>
<link rel="stylesheet" href="https://fonts.googleapis.com/css2?family=Oswald:wght@400&family=Roboto:wght@400;500;700&family=Rubik:wght@500;700&display=swap">
<style>
:root{
  --red:#ee2a35;
  --ink:#222222;
  --text:#444444;
  --muted:#666666;
  --white:#ffffff;
  --light:#f1f1f1;
  --footer:#222222;
  --footer-text:#cfcfcf;
  --line:#3a3a3a;
}
*{box-sizing:border-box;margin:0;padding:0}
html,body{width:1200px;height:4850px;overflow:hidden}
body{position:relative;background:var(--white);font-family:"Roboto",Arial,sans-serif;color:var(--text)}
.abs{position:absolute}
.center{text-align:center}

/* top bar */
.topbar{left:0;top:0;width:1200px;height:32px;background:var(--red);color:var(--white);font-size:13px;font-weight:700;line-height:32px;text-align:center;letter-spacing:.2px}
.topbar svg{position:absolute;top:6px}

/* nav */
.logo{left:143px;top:48px;font-family:"Oswald",sans-serif;font-size:38px;line-height:52px;color:var(--ink);letter-spacing:-.5px}
.menu{right:148px;top:64px;display:flex;gap:28px;font-size:14px;font-weight:500;color:var(--ink)}

/* hero */
.hero{left:0;top:119px;width:1200px;height:704px;background:linear-gradient(180deg,#c8b7a5 0%,#e3d8cc 45%,#b8a898 75%,#8a7a6c 100%)}
.hero-card{left:400px;top:296px;width:400px;height:269px;background:rgba(255,255,255,.93);border:4px solid rgba(255,255,255,.95);outline:2px solid #333;outline-offset:-12px;text-align:center}
.hero-card h1{font-size:38px;font-weight:500;color:var(--ink);margin-top:36px}
.hero-card p{font-size:20px;line-height:29px;color:var(--ink);margin-top:12px}
.btn{display:inline-block;background:var(--red);color:var(--white);font-weight:700;text-align:center;text-transform:uppercase}
.hero-card .btn{position:absolute;left:107px;top:177px;width:184px;height:47px;line-height:47px;font-size:16px}

/* welcome */
.welcome{left:0;top:823px;width:1200px;height:322px;background:var(--red);color:var(--white);text-align:center}
.welcome h2{font-size:31px;font-weight:700;margin-top:78px}
.welcome p{width:820px;margin:22px auto 0;font-size:16.5px;line-height:26px}

/* section titles */
.sec-title{left:0;width:1200px;text-align:center;font-size:32px;font-weight:700;color:var(--ink)}
.rule{left:566px;width:68px;height:3px;background:var(--red)}

/* cards */
.photo{background:linear-gradient(135deg,#8a6a4e,#c9a47c)}
.card-title{font-size:16.5px;font-weight:700;color:var(--ink);text-align:center}
.card-text{font-size:13.5px;line-height:19.5px;color:var(--muted);text-align:center}

/* slider */
.slider{left:0;top:1803px;width:1200px;height:569px;background:linear-gradient(90deg,#3b281c,#5a3e2b 45%,#4a3223 80%,#2f2118)}
.slide-art{left:28px;top:43px;width:556px;height:481px;background:linear-gradient(135deg,#4fb8dc 0%,#e9eef0 45%,#d3b33b 75%,#3b6fb0 100%);opacity:.9;border-radius:6px}
.slide-title{left:625px;top:198px;font-family:"Rubik",sans-serif;font-size:56px;line-height:60px;font-weight:700;color:var(--white)}
.slide-btn{left:629px;top:341px;width:134px;height:38px;line-height:38px;font-size:13px}
.arrow{width:40px;height:40px}

/* featured */
.price{font-size:16.5px;font-weight:500;color:var(--ink);text-align:center}
.outline-btn{width:147px;height:44px;line-height:36px;border:4px solid #f3a8ad;background:var(--red);color:var(--white);font-size:13px;font-weight:700;text-align:center;border-radius:3px}

/* how it works */
.how-title{font-family:"Rubik",sans-serif;letter-spacing:1px}
.how-icon{width:180px;height:141px;border-radius:10px}
.how-step{font-family:"Rubik",sans-serif;font-size:19px;font-weight:500;color:var(--ink);text-align:center}

/* news */
.news{left:0;top:3696px;width:1200px;height:649px;background:var(--light)}
.news-card{width:438px;height:355px}
.news-card h3{position:absolute;left:0;width:100%;top:251px;font-family:"Rubik",sans-serif;font-size:17px;line-height:26px;font-weight:500;color:var(--white);text-align:center}
.news-card .date{position:absolute;left:0;width:100%;top:313px;font-size:13.5px;color:#f5a623;text-align:center}

/* footer */
.footer{left:0;top:4345px;width:1200px;height:505px;background:var(--footer)}
.foot-h{top:4404px;font-family:"Rubik",sans-serif;font-size:22px;font-weight:500;color:var(--white)}
.foot-rule{top:4456px;width:80px;height:1px;background:#555}
.foot-links{left:143px;top:4478px;list-style:none;font-size:14px;line-height:25.7px;color:var(--footer-text)}
.foot-text{font-size:13.5px;line-height:24px;color:var(--footer-text)}
.social{width:30px;height:30px;border:1.5px solid var(--white);border-radius:50%}
.input{left:757px;top:4537px;width:298px;height:41px;background:var(--white);font-size:11px;color:#555;line-height:41px;padding-left:20px}
.join{left:998px;top:4541px;width:53px;height:33px;line-height:33px;font-size:12px}
.foot-divider{left:143px;top:4683px;width:912px;height:1px;background:var(--line)}
.copy{left:0;top:4724px;width:1200px;text-align:center;font-size:13px;color:var(--footer-text)}
.pay{top:4768px;width:50px;height:29px;background:var(--white);border-radius:3px;font-size:9px;font-weight:700;color:var(--ink);text-align:center;line-height:29px}
</style>
</head>
<body>

<header>
  <div class="abs topbar">
    <svg style="left:143px" width="20" height="20" viewBox="0 0 20 20" fill="none" stroke="#fff" stroke-width="1.6" aria-label="Account"><circle cx="10" cy="7" r="4"/><path d="M3 18c1-4 4-5 7-5s6 1 7 5z"/></svg>
    Free shipping on orders over $100
    <svg style="left:993px" width="20" height="20" viewBox="0 0 20 20" fill="none" stroke="#fff" stroke-width="1.8" aria-label="Search"><circle cx="8" cy="8" r="6"/><path d="M12.5 12.5l5 5"/></svg>
    <svg style="left:1030px" width="22" height="20" viewBox="0 0 22 20" fill="none" stroke="#fff" stroke-width="1.6" aria-label="Cart"><path d="M1 2h3l3 11h11l2-8H6"/><circle cx="8" cy="17" r="1.5"/><circle cx="17" cy="17" r="1.5"/></svg>
  </div>
  <div class="abs logo">Otter Bites Guild</div>
  <nav class="abs menu"><span>HOME</span><span>OUR BOXES</span><span>HOW IT WORKS</span><span>SHOP</span><span>CONTACT</span></nav>
</header>

<section class="abs hero" role="img" aria-label="Photo of a dog eating kibble from a steel bowl on a wooden floor"></section>
<div class="abs hero-card">
  <h1>Otter Bites Guild</h1>
  <p>Monthly Subscription of<br>Dog Treats Club</p>
  <span class="btn">Get your box</span>
</div>
<svg class="abs" style="left:588px;top:752px" width="24" height="14" viewBox="0 0 24 14" fill="none" stroke="#222" stroke-width="2.5"><path d="M2 2l10 10L22 2"/></svg>

<section class="abs welcome">
  <h2>WELCOME TO OTTER BITES GUILD</h2>
  <p>Sed ut perspiciatis unde omnis iste natus error sit voluptatem accusantium doloremque laudantium, totam rem aperiam, eaque ipsa quae ab illo inventore veritatis et quasi architecto beatae vitae dicta sunt explicabo. Nemo enim ipsam voluptatem quia voluptas sit aspernatur aut odit aut fugit, sed quia consequuntur magni dolores eos qui ratione voluptatem sequi nesciunt. Neque porro quisquam est, qui dolorem ipsum quia dolor sit amet, consectetur, adipisci velit</p>
</section>

<h2 class="abs sec-title" style="top:1218px">WHAT'S IN A BOX?</h2>
<div class="abs rule" style="top:1274px"></div>

<div class="abs photo" style="left:143px;top:1322px;width:283px;height:251px;background:linear-gradient(135deg,#6e8f4a,#b9a37c 55%,#8a8f95)" role="img" aria-label="Photo of a hand pouring treats into a bowl for a dog"></div>
<div class="abs photo" style="left:458px;top:1322px;width:282px;height:251px;background:radial-gradient(circle at 50% 50%,#8a4a24 0 28%,#4a3324 45%,#2e2119)" role="img" aria-label="Photo of a bowl of kibble on dark wood"></div>
<div class="abs photo" style="left:772px;top:1322px;width:281px;height:251px;background:radial-gradient(circle at 50% 55%,#b58a4c 0 22%,#9a9a9a 40%,#e8e8e8 70%)" role="img" aria-label="Photo of kibble pouring into a steel bowl"></div>

<h3 class="abs card-title" style="left:143px;top:1601px;width:283px">Nemo enim ipsam voluptatem</h3>
<h3 class="abs card-title" style="left:458px;top:1601px;width:282px">Nemo enim ipsam voluptatem</h3>
<h3 class="abs card-title" style="left:772px;top:1601px;width:281px">Nemo enim ipsam voluptatem</h3>
<p class="abs card-text" style="left:150px;top:1636px;width:270px">Sed ut perspiciatis unde omnis iste natus error sit voluptatem accusantium doloremque laudantium, totam rem aperiam, eaque ipsa quae</p>
<p class="abs card-text" style="left:464px;top:1636px;width:270px">Sed ut perspiciatis unde omnis iste natus error sit voluptatem accusantium doloremque laudantium, totam rem aperiam, eaque ipsa quae</p>
<p class="abs card-text" style="left:778px;top:1636px;width:270px">Sed ut perspiciatis unde omnis iste natus error sit voluptatem accusantium doloremque laudantium, totam rem aperiam, eaque ipsa quae</p>

<section class="abs slider">
  <div class="abs slide-art" role="img" aria-label="Illustration of an open subscription box with canned and bagged pet food"></div>
  <h2 class="abs slide-title">What's Inside the<br>Box Each Week</h2>
  <span class="abs btn slide-btn">Shop now</span>
  <svg class="abs arrow" style="left:48px;top:293px" viewBox="0 0 40 40" fill="none" stroke="#ddd" stroke-width="1.5"><circle cx="20" cy="20" r="18"/><path d="M23 12l-8 8 8 8"/></svg>
  <svg class="abs arrow" style="left:1110px;top:293px" viewBox="0 0 40 40" fill="none" stroke="#ddd" stroke-width="1.5"><circle cx="20" cy="20" r="18"/><path d="M17 12l8 8-8 8"/></svg>
</section>

<h2 class="abs sec-title" style="top:2439px">FEATURED PRODUCTS</h2>
<div class="abs rule" style="top:2499px"></div>

<div class="abs" style="left:143px;top:2545px;width:283px;height:334px;background:radial-gradient(circle at 55% 40%,#c33a2c 0 25%,#d9b48a 45%,#8a5a3a)" role="img" aria-label="Photo of bone-shaped biscuits in a red bowl"></div>
<div class="abs" style="left:458px;top:2545px;width:282px;height:334px;background:linear-gradient(135deg,#5a3a22,#a06a3c 50%,#6b4628)" role="img" aria-label="Photo of a pile of brown kibble"></div>
<div class="abs" style="left:772px;top:2545px;width:281px;height:334px;background:linear-gradient(135deg,#3a2818,#b9894e 50%,#5a3e22)" role="img" aria-label="Photo of bone-shaped dog treats close up"></div>

<p class="abs price" style="left:143px;top:2905px;width:283px">$180,00</p>
<p class="abs price" style="left:458px;top:2905px;width:282px">$180,00</p>
<p class="abs price" style="left:772px;top:2905px;width:281px">$180,00</p>
<h3 class="abs card-title" style="left:143px;top:2937px;width:283px">Nemo enim ipsam voluptatem</h3>
<h3 class="abs card-title" style="left:458px;top:2937px;width:282px">Nemo enim ipsam voluptatem</h3>
<h3 class="abs card-title" style="left:772px;top:2937px;width:281px">Nemo enim ipsam voluptatem</h3>
<p class="abs card-text" style="left:160px;top:2969px;width:250px">Sed ut perspiciatis unde omnis iste natus error sit voluptatem</p>
<p class="abs card-text" style="left:474px;top:2969px;width:250px">Sed ut perspiciatis unde omnis iste natus error sit voluptatem</p>
<p class="abs card-text" style="left:788px;top:2969px;width:250px">Sed ut perspiciatis unde omnis iste natus error sit voluptatem</p>
<span class="abs outline-btn" style="left:211px;top:3031px">SHOP NOW</span>
<span class="abs outline-btn" style="left:526px;top:3031px">SHOP NOW</span>
<span class="abs outline-btn" style="left:840px;top:3031px">SHOP NOW</span>

<h2 class="abs sec-title how-title" style="top:3182px">HOW IT WORKS</h2>
<div class="abs rule" style="top:3239px"></div>

<div class="abs how-icon" style="left:185px;top:3301px;background:linear-gradient(180deg,#e9f6fb,#6fa8e8 60%,#f08a2c)" role="img" aria-label="Illustration of a phone showing an order app"></div>
<div class="abs how-icon" style="left:509px;top:3301px;background:linear-gradient(135deg,#f2b12c,#c0392b 50%,#2a6fb0)" role="img" aria-label="Illustration of a bag and a can of pet food"></div>
<div class="abs how-icon" style="left:833px;top:3301px;background:linear-gradient(135deg,#f3e4dc,#c0392b 45%,#9a8a7a)" role="img" aria-label="Illustration of a person serving food to dogs"></div>

<h3 class="abs how-step" style="left:135px;top:3470px;width:280px">1-Nemo enim ipsam</h3>
<h3 class="abs how-step" style="left:459px;top:3470px;width:280px">2-Nemo enim ipsam</h3>
<h3 class="abs how-step" style="left:783px;top:3470px;width:280px">3-Nemo enim ipsam</h3>
<p class="abs card-text" style="left:138px;top:3506px;width:274px;line-height:21px">Lorem Ipsum is simply dummy text of the printing and typesetting industry. Lorem Ipsum has been the industry's standard dummy text ever since</p>
<p class="abs card-text" style="left:462px;top:3506px;width:274px;line-height:21px">Lorem Ipsum is simply dummy text of the printing and typesetting industry. Lorem Ipsum has been the industry's standard dummy text ever since</p>
<p class="abs card-text" style="left:786px;top:3506px;width:274px;line-height:21px">Lorem Ipsum is simply dummy text of the printing and typesetting industry. Lorem Ipsum has been the industry's standard dummy text ever since</p>

<section class="abs news">
  <h2 class="abs sec-title how-title" style="top:70px">RECENT NEWS</h2>
  <div class="abs rule" style="top:129px"></div>
  <article class="abs news-card" style="left:143px;top:192px">
    <div class="abs" style="inset:0;background:linear-gradient(180deg,#4a3a2e,#7a4a2c 50%,#3a2a22)" role="img" aria-label="Photo of a dog wearing a festive hat"></div>
    <h3>Sed Ut Perspiciatis Unde Omnis<br>Sit Voluptatem Accusan</h3>
    <p class="date"><svg width="12" height="12" viewBox="0 0 12 12" fill="none" stroke="#f5a623" stroke-width="1.3"><rect x="1" y="2" width="10" height="9"/><path d="M1 5h10M4 0v3M8 0v3"/></svg>&nbsp; Jan 25, 2020</p>
  </article>
  <article class="abs news-card" style="left:616px;top:192px">
    <div class="abs" style="inset:0;background:linear-gradient(135deg,#3a6aa8,#c07a3a 50%,#5a4a3a)" role="img" aria-label="Photo of a dog reaching toward a hand outdoors"></div>
    <h3>Sed Ut Perspiciatis Unde Omnis<br>Sit Voluptatem Accusan</h3>
    <p class="date"><svg width="12" height="12" viewBox="0 0 12 12" fill="none" stroke="#f5a623" stroke-width="1.3"><rect x="1" y="2" width="10" height="9"/><path d="M1 5h10M4 0v3M8 0v3"/></svg>&nbsp; Jan 25, 2020</p>
  </article>
</section>

<footer>
  <div class="abs footer"></div>
  <h4 class="abs foot-h" style="left:143px">Quick links</h4>
  <h4 class="abs foot-h" style="left:383px">About Otter Bites Guild</h4>
  <h4 class="abs foot-h" style="left:758px">Join our Newsletter</h4>
  <div class="abs foot-rule" style="left:143px"></div>
  <div class="abs foot-rule" style="left:383px"></div>
  <div class="abs foot-rule" style="left:758px"></div>
  <ul class="abs foot-links"><li>Home</li><li>Products</li><li>FAQ</li><li>Track Order</li><li>Previous Boxes</li><li>Contact</li></ul>
  <p class="abs foot-text" style="left:383px;top:4476px;width:300px">Sed ut perspiciatis unde omnis iste natus error sit voluptatem accusantium doloque laudantium, totam rem aperiam, eaque ipsa quae ab illo inventore veritatis et quasi</p>
  <span class="abs social" style="left:386px;top:4595px" aria-label="Social link"></span>
  <span class="abs social" style="left:424px;top:4595px" aria-label="Social link"></span>
  <span class="abs social" style="left:462px;top:4595px" aria-label="Social link"></span>
  <span class="abs social" style="left:499px;top:4595px" aria-label="Social link"></span>
  <p class="abs foot-text" style="left:758px;top:4476px;width:300px;line-height:21px">Subscribe to get special offers, free giveaways, and once-in-a-lifetime deals.</p>
  <div class="abs input">Enter your E - mail</div>
  <span class="abs btn join">JOIN</span>
  <div class="abs foot-divider"></div>
  <p class="abs copy">Otter Bites Guild © 2020 All Rights Reserved</p>
  <span class="abs pay" style="left:510px">CardOne</span>
  <span class="abs pay" style="left:575px">TapWallet</span>
  <span class="abs pay" style="left:640px">Explora</span>
</footer>

</body>
</html>
```